Rollers & Glides.com

Vertical Business Card with focus on branding with our icon. Information on card will be logo, persons name, position, phone number, email address and website. Use the the name Marcus Pellow, position President, phone number 480.915.2267, email Marcus@rollersandglides-demo.com, website www.rollersandglides-demo.com.

```html
<!DOCTYPE html>
<html lang="en">
<head>
<meta charset="utf-8">
<title>Rollers &amp; Glides.com — Business Card</title>
<link rel="stylesheet" href="https://fonts.googleapis.com/css2?family=Roboto:wght@500&family=Arimo:wght@400;700&display=swap">
<style>
  :root {
    --brand-blue: #3461ae;
    --paper: #ffffff;
    --backdrop: #1c1c1c;
  }
  * { box-sizing: border-box; margin: 0; padding: 0; }
  html, body {
    width: 1200px; height: 1015px; overflow: hidden;
    background: var(--backdrop);
  }
  .sheet {
    width: 1200px; height: 1015px;
    display: flex; flex-direction: column; align-items: center; justify-content: center;
    gap: 60px;
  }
  .card {
    position: relative;
    width: 700px; height: 400px;
    overflow: hidden;
    box-shadow: 0 10px 30px rgba(0,0,0,.5);
  }
  .card--front {
    background: var(--brand-blue);
    display: flex; flex-direction: column; align-items: center; justify-content: center;
    gap: 26px;
  }
  .brand-dot {
    width: 86px; height: 86px; border-radius: 50%;
    background: var(--paper);
  }
  .brand-name {
    font-family: "Roboto", sans-serif;
    font-weight: 500;
    font-size: 40px;
    letter-spacing: 3px;
    color: var(--paper);
  }
  .card--back { background: var(--paper); }
  .card__wave { position: absolute; inset: 0; }
  .back-brand {
    position: absolute; left: 70px; top: 60px;
    display: flex; flex-direction: column; align-items: center; gap: 16px;
  }
  .back-brand .brand-dot { width: 62px; height: 62px; background: var(--brand-blue); }
  .back-brand .brand-name { font-size: 28px; letter-spacing: 2px; color: var(--brand-blue); }
  .contact {
    position: absolute; right: 34px; bottom: 48px;
    text-align: right;
    font-family: "Arimo", sans-serif;
    color: var(--paper);
  }
  .contact__name { font-weight: 700; font-size: 26px; letter-spacing: .5px; text-transform: uppercase; }
  .contact__role { font-size: 18px; margin-bottom: 22px; }
  .contact__line {
    display: flex; justify-content: flex-end; align-items: center; gap: 8px;
    font-size: 16px; line-height: 24px;
  }
  .contact__icon { width: 16px; height: 16px; flex: none; }
</style>
</head>
<body>
<main class="sheet">
  <section class="card card--front" aria-label="Card front">
    <span class="brand-dot"></span>
    <h1 class="brand-name">Rollers &amp; Glides.com</h1>
  </section>

  <section class="card card--back" aria-label="Card back">
    <svg class="card__wave" viewBox="0 0 700 400" preserveAspectRatio="none" aria-hidden="true">
      <path fill="var(--brand-blue)" d="M0,300 C230,306 330,250 430,150 C510,75 590,58 700,56 L700,400 L0,400 Z"/>
      <path fill="none" stroke="var(--paper)" stroke-width="5" d="M0,318 C240,324 345,262 445,162 C525,88 600,72 700,70"/>
      <path fill="none" stroke="var(--paper)" stroke-width="4" d="M0,342 C250,346 360,280 462,178 C540,104 610,88 700,86"/>
    </svg>

    <div class="back-brand">
      <span class="brand-dot"></span>
      <p class="brand-name">Rollers &amp; Glides.com</p>
    </div>

    <div class="contact">
      <p class="contact__name">Marcus Pellow</p>
      <p class="contact__role">President</p>
      <p class="contact__line">480.915.2267
        <svg class="contact__icon" viewBox="0 0 24 24" aria-hidden="true"><path fill="#fff" d="M6.6 10.8a15 15 0 0 0 6.6 6.6l2.2-2.2c.3-.3.7-.4 1-.2 1.1.4 2.3.6 3.6.6.6 0 1 .4 1 1V20c0 .6-.4 1-1 1A17 17 0 0 1 3 4c0-.6.4-1 1-1h3.5c.6 0 1 .4 1 1 0 1.3.2 2.5.6 3.6.1.3 0 .7-.2 1z"/></svg>
      </p>
      <p class="contact__line">Marcus@rollersandglides-demo.com
        <svg class="contact__icon" viewBox="0 0 24 24" aria-hidden="true"><rect x="2" y="5" width="20" height="14" fill="#fff"/><path d="M2 5l10 8 10-8" fill="none" stroke="var(--brand-blue)" stroke-width="2"/></svg>
      </p>
      <p class="contact__line">www.rollersandglides-demo.com
        <svg class="contact__icon" viewBox="0 0 24 24" aria-hidden="true"><g fill="none" stroke="#fff" stroke-width="2"><circle cx="12" cy="12" r="10"/><ellipse cx="12" cy="12" rx="4" ry="10"/><path d="M2 12h20M4 7h16M4 17h16"/></g></svg>
      </p>
    </div>
  </section>
</main>
</body>
</html>
```